Meridale Bed Company Needs Business Card

Looking for a very nice looking business card. Creative but not extravagant. We sell beds and pillows across the U.S. and need something professional but catchy. I have attached the logo.

Name : Devin Holt
Title : President
Phone : (800) 471-2960
Email: sleep@quilmora.com
Website: www.quilmora.com

Can be single-sided or double-sided
horizontal or vertical

Can use Blues/Greys

Target Market(s)

Mass Market

Industry/Entity Type

Retail

Contact Information for Business Card

Name : Devin Holt
Title : President
Phone : (800) 471-2960
Email: sleep@quilmora.com
Website: www.quilmora.com

Requirements
Must have
• Clean, Modern, Smooth
• Can use Blues/Greys
• On the other side without the information - have something simple like www.quilmora.com or our logo
Nice to have
• Surprise me
Should not have
• Nothing crazy, nothing cluttered

```html
<!DOCTYPE html>
<html lang="en">
<head>
<meta charset="utf-8">
<title>Meridale Bed Company – Business Card</title>
<link href="https://fonts.googleapis.com/css2?family=Quicksand:wght@300;500;700&display=swap" rel="stylesheet">
<style>
  :root {
    --page: #e6e7e9;
    --card-grey: #9d9e9f;
    --accent-blue: #2ea3d9;
    --line-blue: #7fcaee;
    --white: #ffffff;
    --title-grey: #d6e6ef;
    --photo-warm-a: #efe4d0;
    --photo-warm-b: #c9b89c;
    --photo-cool-a: #e9ecef;
    --photo-cool-b: #8e9297;
    --photo-soft-a: #efe9e4;
    --photo-soft-b: #b9b4b1;
  }
  * { margin: 0; padding: 0; box-sizing: border-box; }
  html, body { width: 1200px; height: 798px; overflow: hidden; }
  body {
    background: var(--page);
    font-family: "Quicksand", "Helvetica Neue", Arial, sans-serif;
  }
  .business-card {
    position: absolute;
    left: 75px;
    top: 99px;
    width: 1050px;
    height: 600px;
    overflow: hidden;
    background: var(--card-grey);
    box-shadow: 0 10px 30px rgba(0,0,0,0.18);
  }
  .card-art { position: absolute; inset: 0; }
  .brand-name {
    position: absolute;
    top: 18px;
    left: 0;
    width: 1050px;
    text-align: center;
    color: var(--white);
    font-weight: 300;
    font-size: 112px;
    letter-spacing: 2px;
    line-height: 1;
  }
  .contact-list {
    position: absolute;
    left: 38px;
    top: 452px;
    list-style: none;
  }
  .contact-item {
    display: flex;
    align-items: center;
    gap: 14px;
    color: var(--white);
    font-weight: 500;
    font-size: 25px;
    height: 38px;
  }
  .contact-icon {
    width: 28px;
    height: 28px;
    flex: none;
  }
  .person {
    position: absolute;
    right: 112px;
    top: 524px;
    text-align: right;
    white-space: nowrap;
  }
  .person-name {
    color: var(--white);
    font-weight: 700;
    font-size: 34px;
    line-height: 1.05;
  }
  .person-title {
    color: var(--title-grey);
    font-weight: 500;
    font-size: 22px;
    line-height: 1.1;
    padding-right: 30px;
  }
  .person-badge {
    position: absolute;
    left: 954px;
    top: 526px;
    width: 62px;
    height: 62px;
  }
</style>
</head>
<body>
  <div class="business-card">
    <svg class="card-art" width="1050" height="600" viewBox="0 0 1050 600">
      <defs>
        <linearGradient id="photoWarm" x1="0" y1="0" x2="1" y2="1">
          <stop offset="0" stop-color="var(--photo-warm-a)"/>
          <stop offset="1" stop-color="var(--photo-warm-b)"/>
        </linearGradient>
        <linearGradient id="photoCool" x1="0" y1="0" x2="0" y2="1">
          <stop offset="0" stop-color="var(--photo-cool-b)"/>
          <stop offset="1" stop-color="var(--photo-cool-a)"/>
        </linearGradient>
        <linearGradient id="photoSoft" x1="1" y1="0" x2="0" y2="1">
          <stop offset="0" stop-color="var(--photo-soft-a)"/>
          <stop offset="1" stop-color="var(--photo-soft-b)"/>
        </linearGradient>
      </defs>

      <path class="photo-panel" role="img" aria-label="Photo of a bed with a cream quilted coverlet and iron headboard"
            d="M0 140 L349 168 L349 460 L0 420 Z" fill="url(#photoWarm)"/>
      <path class="photo-panel" role="img" aria-label="Photo of a bed with a white embroidered comforter in a grey room"
            d="M351 168 L656 193 L656 500 L351 460 Z" fill="url(#photoCool)"/>
      <path class="photo-panel" role="img" aria-label="Photo of a bed with a soft grey damask comforter and upholstered headboard"
            d="M658 193 L1050 225 L1050 560 L658 500 Z" fill="url(#photoSoft)"/>

      <line x1="350" y1="160" x2="350" y2="470" stroke="var(--white)" stroke-width="10"/>
      <line x1="657" y1="185" x2="657" y2="500" stroke="var(--white)" stroke-width="10"/>

      <path class="header-band" d="M0 0 H1050 V235 L0 150 Z" fill="var(--card-grey)"/>
      <line x1="0" y1="150" x2="1050" y2="235" stroke="var(--line-blue)" stroke-width="6"/>

      <path class="contact-panel" d="M-10 409 L590 470 L630 612 L-10 612 Z"
            fill="var(--card-grey)" stroke="var(--white)" stroke-width="8"/>

      <path class="name-panel" d="M600 470 L1062 542 L1062 612 L641 612 Z"
            fill="var(--accent-blue)" stroke="var(--white)" stroke-width="8"/>
    </svg>

    <div class="brand-name">quilmora</div>

    <ul class="contact-list">
      <li class="contact-item">
        <svg class="contact-icon" viewBox="0 0 28 28" aria-hidden="true">
          <rect x="1" y="1" width="26" height="26" rx="6" fill="var(--white)"/>
          <rect x="3.5" y="3.5" width="21" height="21" rx="4" fill="var(--accent-blue)"/>
          <path d="M9 7.5 L12 7.5 L13 11 L11.3 12.4 Q12.6 15.4 15.6 16.7 L17 15 L20.5 16 L20.5 19 Q20.5 20.5 19 20.5 Q8 19.5 7.5 9 Q7.5 7.5 9 7.5 Z" fill="var(--white)"/>
        </svg>
        <span>(800) 471-2960</span>
      </li>
      <li class="contact-item">
        <svg class="contact-icon" viewBox="0 0 28 28" aria-hidden="true">
          <rect x="1" y="1" width="26" height="26" rx="6" fill="var(--white)"/>
          <rect x="3.5" y="3.5" width="21" height="21" rx="4" fill="var(--accent-blue)"/>
          <rect x="7" y="9" width="14" height="10" rx="1" fill="var(--white)"/>
          <path d="M7.5 9.5 L14 14.5 L20.5 9.5" fill="none" stroke="var(--accent-blue)" stroke-width="1.5"/>
        </svg>
        <span>sleep@quilmora.com</span>
      </li>
      <li class="contact-item">
        <svg class="contact-icon" viewBox="0 0 28 28" aria-hidden="true">
          <rect x="1" y="1" width="26" height="26" rx="6" fill="var(--white)"/>
          <rect x="3.5" y="3.5" width="21" height="21" rx="4" fill="var(--accent-blue)"/>
          <g fill="none" stroke="var(--white)" stroke-width="1.4">
            <circle cx="14" cy="14" r="6.5"/>
            <ellipse cx="14" cy="14" rx="3" ry="6.5"/>
            <line x1="7.5" y1="14" x2="20.5" y2="14"/>
          </g>
        </svg>
        <span>www.quilmora.com</span>
      </li>
    </ul>

    <div class="person">
      <div class="person-name">Devin Holt</div>
      <div class="person-title">President</div>
    </div>

    <svg class="person-badge" viewBox="0 0 62 62" aria-hidden="true">
      <circle cx="31" cy="31" r="28" fill="var(--card-grey)" stroke="var(--white)" stroke-width="4"/>
    </svg>
  </div>
</body>
</html>
```